Email Signature Design

Please design an email signature, the below is an example of our current design;
___

HARCOURT ESTATE PARTNERS PTY LTD
DOMINIC FARRADAY
Licensed Strata and Community Manager

148 Calloway Street,
ULTIMO NSW 2007

P: 02.9374.6082 F: 9463.7820
Website: www.harcourtestate.com.au

This e-mail message and accompanying data may contain information that is confidential and private. If you are not the intended recipient, the use, dissemination, distribution or copying of this message or data is prohibited.

If you have received this e-mail in error please notify us immediately and delete all material pertaining to this e-mail. strata@harcourtestate.com.au

___

We would like to incorporate our logo and company colours, you can view the colours and feel of image at www.harcourtestate.com.au

Industry/Entity Type

It Company

Requirements
Must have
• use of logo and company colours (image)

```html
<!DOCTYPE html>
<html lang="en">
<head>
<meta charset="utf-8">
<title>Harcourt Estate Partners – Email Signature</title>
<link rel="stylesheet" href="https://fonts.googleapis.com/css2?family=Source+Sans+3:wght@400;600;700&display=swap">
<style>
  :root {
    --olive: #7d7b3f;
    --sand: #e3d4a9;
    --slate: #6a6b6d;
    --ink: #4f5052;
    --muted: #7a7b7d;
    --rule: #d9d9d9;
    --paper: #ffffff;
  }
  html, body {
    margin: 0;
    padding: 0;
    overflow: hidden;
    background: var(--paper);
  }
  .signature {
    position: relative;
    width: 1200px;
    height: 440px;
    overflow: hidden;
    background: var(--paper);
    font-family: "Source Sans 3", sans-serif;
  }
  .footer-shape {
    position: absolute;
    inset: 0;
  }
  .brand {
    position: absolute;
    left: 142px;
    top: 200px;
    display: flex;
    align-items: center;
    gap: 14px;
  }
  .brand-square {
    width: 36px;
    height: 36px;
    background: var(--olive);
  }
  .brand-name {
    font-weight: 700;
    font-size: 30px;
    letter-spacing: 0.3px;
    color: var(--olive);
    white-space: nowrap;
  }
  .divider {
    position: absolute;
    left: 640px;
    top: 72px;
    width: 1px;
    height: 302px;
    background: var(--rule);
  }
  .details {
    position: absolute;
    left: 668px;
    top: 0;
    margin: 0;
    font-style: normal;
  }
  .details p {
    position: absolute;
    left: 0;
    margin: 0;
    white-space: nowrap;
    line-height: 1;
  }
  .person-name {
    top: 89px;
    font-size: 24px;
    font-weight: 700;
    color: var(--olive);
  }
  .person-role {
    top: 124px;
    font-size: 24px;
    color: var(--muted);
  }
  .company {
    top: 176px;
    font-size: 24px;
    color: var(--olive);
  }
  .address {
    top: 217px;
    font-size: 24px;
    color: var(--ink);
  }
  .contact {
    display: flex;
    align-items: center;
    gap: 10px;
    font-size: 23px;
    color: var(--ink);
  }
  .contact svg {
    width: 22px;
    height: 22px;
    fill: var(--olive);
  }
  .phone { top: 273px; }
  .fax { top: 305px; }
  .email { top: 337px; }
  .website {
    position: absolute;
    left: 720px;
    top: 388px;
    font-size: 23px;
    letter-spacing: 4.6px;
    color: var(--paper);
    white-space: nowrap;
  }
</style>
</head>
<body>
<main class="signature">
  <svg class="footer-shape" viewBox="0 0 1200 440" aria-hidden="true">
    <path d="M0 400 H612 C598 408 588 412 570 412 H0 Z" fill="var(--sand)"/>
    <path d="M0 412 H570 C615 412 628 369 692 368 H1200 V440 H0 Z" fill="var(--slate)"/>
  </svg>

  <div class="brand">
    <span class="brand-square"></span>
    <span class="brand-name">HARCOURT ESTATE PARTNERS</span>
  </div>

  <div class="divider"></div>

  <address class="details">
    <p class="person-name">DOMINIC FARRADAY</p>
    <p class="person-role">Licensed Strata and Community Manager</p>
    <p class="company">HARCOURT ESTATE PARTNERS PTY LTD</p>
    <p class="address">148 Calloway Street, ULTIMO NSW 2007</p>
    <p class="contact phone">
      <svg viewBox="0 0 24 24" aria-label="Phone"><path d="M12 1.5a10.5 10.5 0 1 0 0 21 10.5 10.5 0 0 0 0-21zm0 1.8a8.7 8.7 0 1 1 0 17.4 8.7 8.7 0 0 1 0-17.4zM9 6.5l-1.6.9c-.9.6-.8 2.6.6 5.3 1.4 2.7 3.2 4.3 4.3 4l1.7-.7-1.6-2.8-1.2.5c-.5-.4-1.3-1.8-1.4-2.6l1.1-.7z"/></svg>
      <span>02.9374.6082</span>
    </p>
    <p class="contact fax">
      <svg viewBox="0 0 24 24" aria-label="Fax"><path d="M7 3h8l2 2v4H7zM3 10h18a1 1 0 0 1 1 1v9H2v-9a1 1 0 0 1 1-1zm3 3v2h3v-2zm5 0v2h3v-2zm5 0v2h3v-2zM6 17v1.5h12V17z"/></svg>
      <span>9463.7820</span>
    </p>
    <p class="contact email">
      <svg viewBox="0 0 24 24" aria-label="Email"><path d="M2 9l10-6 10 6v11H2zm3 1.2L12 15l7-4.8V9.6L12 5.4 5 9.6zM8 9h8v1.2H8zm0 2.2h8v1.1H8z"/></svg>
      <span>strata@harcourtestate.com.au</span>
    </p>
  </address>

  <p class="website">www.harcourtestate.com.au</p>
</main>
</body>
</html>
```